Hi Designers,

I will need 4 web pages designed. The web page looks like an App (if you click on the logo, or the icon on an iPad, it will take you to the website), but it is still a webpage.

Please check the attachment on this brief to understand what specific pages I need to be designed.

A .PSD (straight-up PhotoShop image) as final deliverable is fine, as long as you give us the exact “web color numbers”.

The design is for desktop and iPad but in a single unified web application, NOT separate web app and (native) iPad app.

Details:

Brightwater Policy Partners is developing a browser-based application for use on any mobile device or desktop. The app will be used by corporations to communicate with their employees regarding legal, regulatory and company requirements for conducting business. The app is known as “Harbor Guidance Portal.” When the user clicks on the icon for Harbor Guidance Portal, they will enter a site full of information that a company deems necessary for the employee to do his/her job. There are several content sections within the site, including a login page, training, policies, forms, news feeds and blogs.

The application has been built using Microsoft .NET, and fully supports CSS-type skinning; it uses traditional page layouts. We are seeking a product logo concept (image), a master application/desktop icon (image), as well as a full color scheme/theme/skin design for all areas of the application (header area, body text, menu bar, etc.) in the form of a CSS. The look should be clean, crisp and professional; nothing cartoony or whimsical. It should be easy to read and “airy”.

We have sketched prototypes for the basic application page layout that we can send as a next step of the process.
Updates

Screen shots have been uploaded to this project.  Please use them to guide your design.

Dear designers,

I apologize for the delay in providing feedback. My partners and I will provide feedback in a few days. Thank you for your patience.

Industry/Entity Type

Business

Font styles to use
Other font styles liked:
• see font on screen shots when uploaded

```html
<!DOCTYPE html>
<html lang="en">
<head>
<meta charset="utf-8">
<title>Harbor Guidance Portal – Sign In</title>
<link href="https://fonts.googleapis.com/css2?family=Open+Sans:ital,wght@0,400;0,600;1,400&display=swap" rel="stylesheet">
<style>
  :root {
    --bg-top: #5b91c9;
    --bg-mid: #2f6f9f;
    --bg-bottom: #0f4a70;
    --panel: #f2f2f2;
    --panel-edge: #e6e6e6;
    --card: #fbfbfb;
    --card-border: #e3e3e3;
    --label: #666a6e;
    --placeholder: #9a9a9a;
    --input-bg: #f4f4f4;
    --input-border: #d6d6d6;
    --brand-navy: #0c3566;
    --brand-blue: #2a5b95;
    --button-top: #66b23a;
    --button-bottom: #4a9426;
    --button-border: #3f8420;
    --white: #ffffff;
  }
  * { box-sizing: border-box; margin: 0; padding: 0; }
  html, body { width: 1200px; height: 801px; overflow: hidden; }
  body {
    position: relative;
    font-family: "Open Sans", Arial, sans-serif;
    background: linear-gradient(180deg, var(--bg-top) 0%, var(--bg-mid) 50%, var(--bg-bottom) 100%);
  }
  .login-panel {
    position: absolute;
    left: 110px; top: 68px;
    width: 980px; height: 659px;
    background: linear-gradient(135deg, #f6f6f6 0%, var(--panel) 45%, #ececec 100%);
    border: 1px solid var(--panel-edge);
    border-radius: 2px;
    box-shadow: 0 1px 4px rgba(0,0,0,0.25);
  }
  .product-brand {
    position: absolute;
    left: 373px; top: 56px;
    width: 230px; height: 97px;
    background: var(--brand-navy);
    border-radius: 3px;
    display: flex; align-items: center; justify-content: center; gap: 14px;
  }
  .product-brand .mark {
    width: 22px; height: 22px;
    background: var(--white);
    border-radius: 50%;
  }
  .product-brand .name {
    color: var(--white);
    font-size: 19px;
    font-weight: 400;
  }
  .login-card {
    position: absolute;
    left: 267px; top: 192px;
    width: 448px; height: 289px;
    background: var(--card);
    border: 1px solid var(--card-border);
    border-radius: 3px;
  }
  .field-label {
    position: absolute;
    left: 25px;
    font-size: 14px;
    color: var(--label);
  }
  .field-input {
    position: absolute;
    left: 135px;
    width: 293px; height: 37px;
    background: var(--input-bg);
    border: 1px solid var(--input-border);
    border-radius: 2px;
    padding-left: 13px;
    display: flex; align-items: center;
    font-size: 11.5px;
    font-style: italic;
    color: var(--placeholder);
  }
  .label-user { top: 43px; }
  .input-user { top: 37px; }
  .label-pass { top: 105px; }
  .input-pass { top: 99px; }
  .options-row {
    position: absolute;
    left: 140px; top: 161px;
    display: flex; align-items: center;
    font-size: 13px;
    color: var(--label);
  }
  .checkbox {
    width: 13px; height: 13px;
    border: 1px solid #cfcfcf;
    background: #f0f0f0;
    border-radius: 2px;
    margin-right: 13px;
  }
  .divider { margin: 0 17px 0 12px; }
  .sign-in {
    position: absolute;
    left: 344px; top: 216px;
    width: 86px; height: 35px;
    background: linear-gradient(180deg, var(--button-top), var(--button-bottom));
    border: 1px solid var(--button-border);
    border-radius: 2px;
    color: var(--white);
    font-size: 14px;
    display: flex; align-items: center; justify-content: center;
  }
  .portal-brand {
    position: absolute;
    left: 368px; top: 524px;
    width: 216px; height: 102px;
    background: #f5f5f5;
    display: flex; align-items: center; gap: 12px;
    padding-left: 24px;
  }
  .portal-brand .mark {
    width: 36px; height: 36px;
    border-radius: 50%;
    background: var(--brand-blue);
    flex: none;
  }
  .portal-brand .name {
    color: var(--brand-blue);
    font-size: 20px;
    line-height: 29px;
    font-weight: 400;
    text-transform: uppercase;
  }
  .copyright {
    position: absolute;
    left: 0; right: 0; top: 755px;
    text-align: center;
    font-size: 13px;
    color: var(--white);
  }
</style>
</head>
<body>
  <main class="login-panel">
    <div class="product-brand">
      <span class="mark"></span>
      <span class="name">Veltrix Labs</span>
    </div>

    <form class="login-card">
      <span class="field-label label-user">User name :</span>
      <div class="field-input input-user">Enter user name...</div>
      <span class="field-label label-pass">Password :</span>
      <div class="field-input input-pass">Enter your Password...</div>
      <div class="options-row">
        <span class="checkbox"></span>
        <span>Keep me Signed in</span>
        <span class="divider">|</span>
        <span>Forgot Password?</span>
      </div>
      <div class="sign-in">SIGN IN</div>
    </form>

    <div class="portal-brand">
      <span class="mark"></span>
      <span class="name">Harbor<br>Guidance<br>Portal</span>
    </div>
  </main>

  <footer class="copyright">(c) 2013 Harbor Guidance Portal. All Right Reserved.</footer>
</body>
</html>
```